Accounting firm needs a flyer "Brevora Group".. many job after this Stationary, business card

We need a flyer for a new company based in Melbourne Australia. We are group of young professionals who intend to provide various accounting services, taxation, finance, bookkeeping and payroll, Business service service advisory and management consulting.The main task of the firm is to provide accounting and taxation services. we then use our associates/referral partners to assist client with their legal, migration, finance needs.

We would like to see designs that match our logo, business card and letter head which I have uploaded along with this. I have also uploaded some of our website contents that might be used in flyers.
My favorite colors are: Blue (navy and royal blue), Teal (blue green), Turquoise, purple(orchid, lavender, plum).

Our brand:
Brevora Group
Where counsel runs deeper

Our mission:
To group the professionals in house, Where counsel runs deeper and turn into better business for our people, for our clients and four our communities.

We like our logo, however we are still not sure about our business card. So if we are open to work with someone who works with flyers and business card at the same time .

Target Market(s)

Individual and business client in Australia

Industry/Entity Type

Finance And Accounting

Colors
0255a3
3176b5
0493ce
33a6d7
886aae
b768aa
00a990
33b8a4

Requirements
Must have
• Brevora Group logo
• Liability limited by a scheme approved under the professional standards legislation
• Our motto: Brevora Group where counsel runs deeper
• Short description of our services:
• • Bookkeeping & Payroll
• • Finance & Capital Raising
• • Taxation, Accounting and compliances
• • Business service and advisory
• • Migration
• • ASIC and Corporate Secretarial
• • Business law and legal services
• About us
• BREVORA aim to be more than just an accounting firm. We support our clients to help them achieve their personal and business goals by offering a fully integrated advisory service, helping clients to build wealth and protect their assets.We will bring together the relevant professionals across a number of specialties and locations; providing a responsive, personalised solution.
• Our mission: To group the professionals in house, Where counsel runs deeper and turn into better business for our people, for our clients and four our communities.
Nice to have
• Tax agent logo
• FLT logo

```html
<!DOCTYPE html>
<html lang="en">
<head>
<meta charset="utf-8">
<title>Brevora Group Flyer</title>
<link href="https://fonts.googleapis.com/css2?family=Open+Sans:wght@400;600;700;800&display=swap" rel="stylesheet">
<style>
:root{
  --navy:#0255a3;
  --royal:#3176b5;
  --sky:#0493ce;
  --sky-light:#33a6d7;
  --purple:#886aae;
  --orchid:#b768aa;
  --teal:#00a990;
  --teal-light:#33b8a4;
  --ink:#1d2b3a;
  --muted:#5a6673;
  --stage:#e4e6e9;
  --paper:#ffffff;
}
*{margin:0;padding:0;box-sizing:border-box}
html,body{width:1200px;height:1000px;overflow:hidden;background:var(--stage)}
body{font-family:"Open Sans",Arial,sans-serif;color:var(--ink)}
.flyer{position:absolute;left:275px;top:40px;width:650px;height:920px;background:var(--paper);overflow:hidden;box-shadow:0 4px 18px rgba(0,0,0,.18)}
.hero{position:absolute;left:0;top:0;width:650px;height:300px;
  background:linear-gradient(120deg,#4a3a3e 0%,#8a7a70 30%,#d8d2c8 55%,#f2efe9 75%,#c9b79a 100%)}
.brand{position:absolute;left:28px;top:22px;display:flex;flex-direction:column;align-items:center;gap:6px}
.brand-mark{width:92px;height:92px;border-radius:50%;background:var(--navy);border:4px solid #fff}
.brand-name{font-weight:800;font-size:21px;color:var(--navy);background:#fff;padding:1px 8px;letter-spacing:1px}
.brand-motto{font-size:10px;font-weight:600;color:var(--navy);background:#fff;padding:1px 6px}
.badges{position:absolute;right:26px;top:170px;display:flex;gap:10px;align-items:center}
.badge-tax{width:34px;height:34px;border-radius:50%;background:#d9b300;border:3px solid #fff}
.badge-flt{width:70px;height:30px;background:#fff}
.accent{position:absolute;left:0;top:262px;width:650px;height:40px}
.body{position:absolute;left:0;top:306px;width:650px;height:514px;display:flex;flex-direction:column}
.intro{padding:0 30px;font-size:9.5px;line-height:1.35}
.intro h3{font-size:11.5px;font-weight:700;color:var(--navy);margin-top:4px}
.intro .values{color:var(--navy);font-weight:700}
.services-head{position:relative;height:26px;margin-top:8px;flex:none}
.services-head svg{position:absolute;left:0;top:0;width:650px;height:26px}
.services-title{position:relative;text-align:center;color:#fff;font-weight:700;font-size:14px;line-height:26px}
.services{padding:10px 30px 0;display:grid;grid-template-columns:1fr 1fr;column-gap:24px}
.service{font-size:9.5px;line-height:1.35;text-align:justify;margin-bottom:8px}
.service b{color:var(--navy);font-weight:700}
.service b::before{content:"";display:inline-block;width:6px;height:6px;background:var(--teal);margin-right:5px;vertical-align:1px}
.legal{margin-top:auto;padding:0 30px 4px;font-size:8.5px;color:var(--muted)}
.footer{position:absolute;left:0;top:826px;width:650px;height:94px}
.contact{position:absolute;color:#fff;font-weight:600;font-size:13px;display:flex;align-items:center;gap:6px;white-space:nowrap}
.contact.email{left:318px;top:841px}
.contact.phone{left:530px;top:841px}
.contact.web{left:26px;top:885px}
</style>
</head>
<body>
<main class="flyer">
  <div class="hero" role="img" aria-label="Photograph of a person working on a laptop at a wooden desk by a bright window"></div>
  <div class="brand">
    <span class="brand-mark"></span>
    <span class="brand-name">BREVORA</span>
    <span class="brand-motto">Where counsel runs deeper</span>
  </div>
  <div class="badges">
    <span class="badge-tax"></span>
    <span class="badge-flt"></span>
  </div>
  <svg class="accent" viewBox="0 0 650 40" aria-hidden="true">
    <polygon points="0,22 650,0 650,22 0,40" fill="#fff"/>
    <polygon points="0,26 650,4 650,12 0,34" fill="var(--orchid)"/>
  </svg>

  <div class="body">
    <section class="intro">
      <h3>Our Mission :</h3>
      <p>To group the professionals in house, where counsel runs deeper and turn into better business for our people, for our clients and four our communities.</p>
      <h3>Our Firm :</h3>
      <p>As a group of professionals, our firm are available to provide you with high quality accounting, taxation and business advisory whether you are a business owner, family or an individual client. We have a strategic alliance with our referral lawyers, migration agents and mortgage brokers.
      <span class="values">Our core values include expertise, confidentiality, teamwork and commitment.</span></p>
      <h3>About Us :</h3>
      <p>Brevora aim to be more than just an accounting firm. We support our clients to help them achieve their personal and business goals by offering a fully integrated advisory service, helping clients to build wealth and protect their assets. We bring together the relevant professionals across a number of specialties and locations, providing a responsive, personalised solution.</p>
    </section>

    <div class="services-head">
      <svg viewBox="0 0 650 26" aria-hidden="true"><polygon points="0,3 650,0 650,23 0,26" fill="var(--teal)"/></svg>
      <h2 class="services-title">Our Services :</h2>
    </div>

    <section class="services">
      <div class="col">
        <p class="service"><b>Bookkeeping &amp; Payroll</b> Our bookkeeping involves maintaining accurate and updated records of all your business and personal financial activities. We manage your payroll on an ongoing basis, ensuring that all employees are compensated according to their employment agreements.</p>
        <p class="service"><b>Finance &amp; Capital Raising</b> We regularly review client portfolios to identify opportunities and refer them to experienced and professional finance brokers to save and assist them with renegotiating a better deal with their current lender or seek out a better loan from a different lender.</p>
        <p class="service"><b>Taxation, Accounting and Compliances</b> At Brevora experienced tax agent build close working relationships with you to understand your circumstances and develop customised solutions for your personal income tax and corporate tax exposure.</p>
      </div>
      <div class="col">
        <p class="service"><b>Business Services and Advisory</b> While we provide peace of mind through taking care of the usual accounting and tax compliance matters, our real value lies in seeking to help you address business challenges and uncover opportunities.</p>
        <p class="service"><b>Migration</b> The business innovation visa or Employer Business Sponsored visa application can be complex with the requirement to submit various business, financial and asset documents.</p>
        <p class="service"><b>ASIC and Corporate Secretarial</b> Brevora understand that your corporate register, minutes and officeholder information and other secretarial register must kept for the life of the entity. Therefore, we maintain these documents.</p>
        <p class="service"><b>Business law and legal services</b> When it comes to business law and legal services, you want to ensure you have a trusted competent legal team to work alongside with your accountants to help you across the broad range of commercial circumstances.</p>
      </div>
    </section>

    <p class="legal">Liability limited by a scheme approved under the professional standards legislation.</p>
  </div>

  <svg class="footer" viewBox="0 0 650 94" aria-hidden="true">
    <polygon points="300,0 650,0 650,46 260,46" fill="var(--navy)"/>
    <polygon points="0,46 650,46 650,94 0,94" fill="var(--sky-light)"/>
    <polygon points="0,46 280,46 250,94 0,94" fill="var(--sky)"/>
  </svg>
  <p class="contact email">
    <svg width="14" height="11" viewBox="0 0 14 11" aria-hidden="true"><rect x="0.5" y="0.5" width="13" height="10" rx="1" fill="none" stroke="#fff"/><polyline points="1,1 7,6 13,1" fill="none" stroke="#fff"/></svg>
    hello@brevoragroup.com.au</p>
  <p class="contact phone">
    <svg width="12" height="14" viewBox="0 0 12 14" aria-hidden="true"><rect x="1.5" y="0.5" width="9" height="13" rx="2" fill="none" stroke="#fff"/><circle cx="6" cy="11" r="1" fill="#fff"/></svg>
    0412 555 019</p>
  <p class="contact web">
    <svg width="13" height="13" viewBox="0 0 13 13" aria-hidden="true"><circle cx="6.5" cy="6.5" r="6" fill="none" stroke="#fff"/><ellipse cx="6.5" cy="6.5" rx="2.5" ry="6" fill="none" stroke="#fff"/><line x1="0.5" y1="6.5" x2="12.5" y2="6.5" stroke="#fff"/></svg>
    www.brevoragroup.com.au</p>
</main>
</body>
</html>
```